Heritage Hollow Business Cards

Require a business card design. <br/><br/>Needs to include logo (either round or long version) plus these details:<br/>Maya Torvell<br/>Heritage Hollow<br/>maya@kelvadtrading.com.au<br/>02 6481 7395<br/>PO Box Glenwarra NSW 2791<br/>www.heritagehollow.com.au<br/><br/>I need in an editable format so that I can create for multiple staff members. <br/><br/>

Target Market(s)

We are an online store selling renovation products to home owners are builders. Looking for a classic classy design.

Industry/Entity Type

Home And Garden

Contact Information for Business Card

Maya Torvell
Heritage Hollow
maya@kelvadtrading.com.au
02 6481 7395
PO Box Glenwarra NSW 2791
www.heritagehollow.com.au

Colors

Designer to choose colors to be used in the design.

Requirements
Must have
• Must include Logo.

```html
<!DOCTYPE html>
<html lang="en">
<head>
<meta charset="utf-8">
<title>Heritage Hollow Business Cards</title>
<link href="https://fonts.googleapis.com/css2?family=Arimo:wght@400;700&display=swap" rel="stylesheet">
<style>
  :root {
    --backdrop: #e4e2de;
    --card: #1f1f1f;
    --card-shade: #262626;
    --ink: #ffffff;
    --rule: #9a9a9a;
    --sketch-tone: #2b2b2b;
  }
  html, body {
    margin: 0;
    width: 1200px;
    height: 900px;
    overflow: hidden;
    background: var(--backdrop);
    font-family: "Arimo", Arial, sans-serif;
  }
  .canvas { position: relative; width: 1200px; height: 900px; }
  .card {
    position: absolute;
    background: var(--card);
    color: var(--ink);
    overflow: hidden;
    box-shadow: 0 3px 8px rgba(0,0,0,.35);
  }
  .card--front { left: 330px; top: 90px; width: 555px; height: 345px; }
  .card--back { left: 330px; top: 470px; width: 560px; height: 343px; background: linear-gradient(160deg, var(--card-shade), var(--card)); }
  .roof-sketch {
    position: absolute; inset: 0;
    background:
      linear-gradient(135deg, transparent 45%, var(--sketch-tone) 46%, var(--sketch-tone) 52%, transparent 53%),
      linear-gradient(225deg, transparent 45%, var(--sketch-tone) 46%, var(--sketch-tone) 52%, transparent 53%),
      radial-gradient(ellipse at 50% 90%, #2a2a2a, var(--card) 70%);
    opacity: .8;
  }
  .front-content {
    position: absolute; inset: 0;
    text-align: center;
  }
  .staff-name {
    position: absolute; top: 66px; left: 0; right: 0;
    margin: 0; font-size: 24px; font-weight: 700; letter-spacing: .5px;
  }
  .icon-row {
    position: absolute; top: 114px; left: 188px; width: 178px; height: 22px;
    display: flex; align-items: center; gap: 5px;
  }
  .icon-row .rule { flex: 1; height: 1px; background: var(--rule); }
  .icon { width: 22px; height: 22px; display: block; }
  .contact-list {
    position: absolute; top: 148px; left: 0; right: 0;
    margin: 0; padding: 0; list-style: none;
    font-size: 16px; line-height: 20.5px;
  }
  .divider { position: absolute; top: 221px; left: 185px; width: 183px; height: 1px; background: var(--rule); }
  .company-name { position: absolute; top: 240px; left: 0; right: 0; margin: 0; font-size: 16px; font-weight: 700; }
  .company-address { position: absolute; top: 259px; left: 0; right: 0; margin: 0; font-size: 16px; }
  .brand {
    position: absolute; left: 0; right: 0; top: 150px;
    display: flex; justify-content: center; align-items: center; gap: 14px;
  }
  .brand-mark { width: 34px; height: 34px; border-radius: 50%; border: 2px solid var(--ink); box-sizing: border-box; }
  .brand-name { font-size: 36px; font-weight: 400; color: var(--ink); }
</style>
</head>
<body>
<main class="canvas">
  <section class="card card--front">
    <div class="roof-sketch" role="img" aria-label="Faint hand-drawn sketch of a heritage house roof gable"></div>
    <div class="front-content">
      <h1 class="staff-name">MAYA TORVELL</h1>
      <div class="icon-row">
        <span class="rule"></span>
        <svg class="icon" viewBox="0 0 22 22" aria-label="Phone"><rect width="22" height="22" rx="3" fill="#fff"/><path d="M6 9c0-2 2-3 5-3s5 1 5 3l-2 1-1-1.5h-4L8 10zM7 11h8l1 5H6z" fill="#1f1f1f"/></svg>
        <svg class="icon" viewBox="0 0 22 22" aria-label="Email"><rect width="22" height="22" rx="3" fill="#fff"/><rect x="5" y="7" width="12" height="8" fill="none" stroke="#1f1f1f" stroke-width="1.4"/><path d="M5 7l6 5 6-5" fill="none" stroke="#1f1f1f" stroke-width="1.4"/></svg>
        <svg class="icon" viewBox="0 0 22 22" aria-label="Website"><rect width="22" height="22" rx="3" fill="#fff"/><circle cx="11" cy="11" r="6" fill="#1f1f1f"/><path d="M8 8c2 0 3 2 2 3s-2 1-1 3M13 7c0 2 2 2 3 3" stroke="#fff" stroke-width="1.2" fill="none"/></svg>
        <span class="rule"></span>
      </div>
      <ul class="contact-list">
        <li>02 6481 7395</li>
        <li>maya@kelvadtrading.com.au</li>
        <li>www.heritagehollow.com.au</li>
      </ul>
      <div class="divider"></div>
      <p class="company-name">HERITAGE HOLLOW</p>
      <p class="company-address">PO Box Glenwarra NSW 2791</p>
    </div>
  </section>
  <section class="card card--back">
    <div class="brand">
      <span class="brand-mark"></span>
      <span class="brand-name">Heritage Hollow</span>
    </div>
  </section>
</main>
</body>
</html>
```